Retail Jewelry Business Card Design Project

We are in need of a new business card design for a retail jewelry store. This store is in the business of fine jewelry including but not specific to bridal jewelry, diamonds, designer jewelry and watches.

This store has been in business for 20 years but continues to strive for a modern professional appeal. The main colors use for this business are a royal blue, white and silver.

Target Market(s)

Target market is ages 18-50

Industry/Entity Type

Jewelry

Requirements
Must have
• Sales Person Name
Sales Person Email Address

Store Address
Store Phone
Website

Standard business card size. No odd shapes or sizes.
Nice to have
• Overall modern feel for card.

We have thought that a design with a nice feature of the logo on the back of the card would be nice but open to ideas.
Should not have
• No specific images of jewelry should be used.

```html
<!DOCTYPE html>
<html lang="en">
<head>
<meta charset="utf-8">
<title>Harlan Reed Fine Jewelry – Business Cards</title>
<link rel="stylesheet" href="https://fonts.googleapis.com/css2?family=Tinos:ital,wght@0,400;0,700;1,700&family=Arimo:wght@400&display=swap">
<style>
  :root {
    --royal-blue: #2b2c9b;
    --lavender: #7b78c6;
    --ink-grey: #555559;
    --card-white: #ffffff;
    --backdrop: #e9e9ec;
    --rule-grey: #c9c9cf;
  }
  * { box-sizing: border-box; margin: 0; padding: 0; }
  html, body { width: 1200px; height: 804px; overflow: hidden; }
  body {
    background: var(--backdrop);
    position: relative;
    font-family: "Tinos", "Times New Roman", serif;
  }
  .card {
    position: absolute;
    top: 247px;
    width: 540px;
    height: 309px;
    background: var(--card-white);
    box-shadow: 0 2px 10px rgba(0,0,0,0.12);
    overflow: hidden;
  }
  .card--contact { left: 40px; }
  .card--brand { left: 620px; }

  .wordmark {
    position: absolute;
    color: var(--royal-blue);
    font-family: "Tinos", "Times New Roman", serif;
    font-weight: 700;
    text-align: center;
    line-height: 1.05;
  }
  .card--contact .wordmark { left: 40px; top: 36px; width: 320px; font-size: 38px; }
  .card--brand .wordmark { left: 0; top: 78px; width: 540px; font-size: 50px; }

  .card-band { position: absolute; left: 0; bottom: 0; width: 540px; height: 60px; }

  .person {
    position: absolute;
    left: 56px;
    top: 176px;
    width: 240px;
    text-align: center;
  }
  .person-name {
    color: var(--royal-blue);
    font-weight: 700;
    font-style: italic;
    font-size: 15px;
    letter-spacing: 0.5px;
    margin-bottom: 6px;
  }
  .person-address {
    color: var(--ink-grey);
    font-size: 13px;
    line-height: 1.3;
  }
  .divider {
    position: absolute;
    left: 318px;
    top: 140px;
    width: 1px;
    height: 92px;
    background: var(--rule-grey);
  }
  .contact-list {
    position: absolute;
    left: 332px;
    top: 142px;
    list-style: none;
    color: var(--ink-grey);
    font-size: 12.5px;
  }
  .contact-item { display: flex; align-items: center; gap: 6px; height: 22px; }
  .contact-icon { width: 12px; height: 12px; flex: none; }

  .site-address {
    position: absolute;
    left: 0;
    top: 236px;
    width: 540px;
    text-align: center;
    font-family: "Arimo", Arial, sans-serif;
    font-size: 15px;
    letter-spacing: 2.5px;
    color: var(--ink-grey);
  }
</style>
</head>
<body>

<section class="card card--contact" aria-label="Business card, contact side">
  <div class="wordmark">Harlan Reed<br>Fine Jewelry</div>

  <div class="person">
    <p class="person-name">Harlan Reed Whitmore</p>
    <p class="person-address">2750 Marlow Avenue<br>Bayport, FL 32999</p>
  </div>

  <div class="divider"></div>

  <ul class="contact-list">
    <li class="contact-item">
      <svg class="contact-icon" viewBox="0 0 12 12" aria-hidden="true">
        <circle cx="6" cy="6" r="6" fill="var(--ink-grey)"/>
        <path d="M4 3 L5 3 L5.6 4.6 L4.9 5.2 Q5.6 6.6 6.8 7.1 L7.4 6.4 L9 7 L9 8 Q6 9 3.5 5 Q3.3 3.6 4 3 Z" fill="#fff"/>
      </svg>
      555-014-2280
    </li>
    <li class="contact-item">
      <svg class="contact-icon" viewBox="0 0 12 12" aria-hidden="true">
        <circle cx="6" cy="6" r="6" fill="var(--ink-grey)"/>
        <rect x="3" y="4" width="6" height="4.2" fill="#fff"/>
        <path d="M3 4 L6 6.4 L9 4" fill="none" stroke="var(--ink-grey)" stroke-width="0.7"/>
      </svg>
      harlan@harlanreedjewelry.com
    </li>
    <li class="contact-item">
      <svg class="contact-icon" viewBox="0 0 12 12" aria-hidden="true">
        <circle cx="6" cy="6" r="6" fill="var(--ink-grey)"/>
        <circle cx="6" cy="6" r="3.4" fill="none" stroke="#fff" stroke-width="0.8"/>
        <ellipse cx="6" cy="6" rx="1.4" ry="3.4" fill="none" stroke="#fff" stroke-width="0.7"/>
        <line x1="2.6" y1="6" x2="9.4" y2="6" stroke="#fff" stroke-width="0.7"/>
      </svg>
      www.harlanreedjewelry.com
    </li>
  </ul>

  <svg class="card-band" viewBox="0 0 540 60" aria-hidden="true">
    <polygon points="360,18 540,4 540,16 350,40" fill="var(--lavender)"/>
    <polygon points="0,44 336,44 318,60 0,60" fill="var(--royal-blue)"/>
  </svg>
</section>

<section class="card card--brand" aria-label="Business card, brand side">
  <div class="wordmark">Harlan Reed<br>Fine Jewelry</div>
  <p class="site-address">www.harlanreedjewelry.com</p>
</section>

</body>
</html>
```